Military and tactical gear supply company needs web design

We need a web design for a company called U.S. Torvane. We provide quality tactical equipment to military and law enforcement. This is an e-commerce business and we primarily market ourselves on social media. Our key products are backpacks, military-style belts, and tactical flashlights. The gear we sell is not yet widely known about, but is on par with the state-of-the-art products in this field. We want the website to convey the message of quality, durability, and reliability. We use the word "kinetic" because the customers in this field are very "action-oriented" and we would like that idea to be communicated in the web site as well. The primary demographic is men in their 20's-30's, so the web site should have a masculine feel to it. Attached is the logo and color scheme.

```html
<!DOCTYPE html>
<html lang="en">
<head>
<meta charset="utf-8">
<title>U.S. Torvane — Tactical Gear</title>
<link href="https://fonts.googleapis.com/css2?family=Arimo:wght@400;700&family=Open+Sans:ital,wght@0,400;0,600;0,700;1,400&display=swap" rel="stylesheet">
<style>
  :root{
    --blue:#2f6580;
    --blue-dark:#244f66;
    --red:#b5202e;
    --ink:#222;
    --text:#3a3a3a;
    --muted:#777;
    --line:#d6d6d6;
    --dark:#1f1f1f;
    --star:#f2c200;
    --white:#fff;
  }
  *{box-sizing:border-box;margin:0;padding:0}
  html,body{width:1200px;height:4166px;overflow:hidden;background:var(--white)}
  body{font-family:"Arimo",Arial,sans-serif;color:var(--text)}
  .page{position:relative;width:1200px;height:4166px;overflow:hidden}
  .abs{position:absolute}

  /* header */
  .site-header{position:absolute;top:0;left:0;width:1200px;height:98px;background:var(--white);z-index:3}
  .brand{position:absolute;left:110px;top:28px;font:700 36px/44px "Arimo",Arial,sans-serif;color:var(--blue-dark);letter-spacing:1px}
  .nav{position:absolute;top:41px;left:493px;display:flex;gap:37px;font-size:17px;color:var(--ink);list-style:none}
  .nav .active{color:var(--red)}

  /* hero */
  .hero{position:absolute;top:98px;left:0;width:1200px;height:640px;
    background:linear-gradient(180deg,#7d8a91 0%,#a39a86 40%,#8a7860 70%,#6e604c 100%)}
  .hero-title{position:absolute;top:265px;width:1200px;text-align:center;font:700 72px/1 "Open Sans",sans-serif;color:var(--white);text-shadow:0 3px 8px rgba(0,0,0,.5)}
  .hero-sub{position:absolute;top:370px;width:1200px;text-align:center;font:400 24px/41px "Open Sans",sans-serif;color:var(--white);text-shadow:0 2px 5px rgba(0,0,0,.6)}
  .btn-start{position:absolute;top:478px;left:515px;width:170px;height:52px;border-radius:26px;background:var(--white);color:var(--ink);font:400 23px/52px "Open Sans",sans-serif;text-align:center}
  .hero-dots{position:absolute;top:658px;left:570px;display:flex;gap:14px}
  .hero-dots span{width:10px;height:10px;border-radius:50%;background:var(--white)}
  .hero-curve{position:absolute;top:600px;left:0}

  /* headings */
  .heading{font:700 40px/1 "Arimo",Arial,sans-serif;color:var(--ink);text-transform:uppercase}
  .heading em{font-style:normal;color:var(--red)}

  /* about */
  .about-title{left:122px;top:826px}
  .about-text{left:120px;top:880px;width:555px;font-size:17px;line-height:37px;text-align:justify}
  .btn-more{left:122px;top:1232px;width:128px;height:50px;border-radius:25px;background:var(--blue);color:var(--white);font:700 17px/50px "Arimo",sans-serif;text-align:center}
  .about-arc{left:731px;top:868px;width:344px;height:344px;border-radius:50%;background:var(--blue)}
  .about-photo{left:735px;top:847px;width:336px;height:336px;border-radius:50%;
    background:radial-gradient(circle at 45% 40%,#8c8a78 0%,#a7997c 45%,#cbbf9f 100%)}

  /* why choose */
  .why{position:absolute;top:1347px;left:0;width:1200px;height:580px;
    background:linear-gradient(100deg,#2a2d33 0%,#3b3a3c 35%,#4a4744 60%,#2b2b2b 85%,#222 100%)}
  .why-title{top:80px;width:1200px;text-align:center;color:var(--white)}
  .feature{position:absolute;top:178px;width:320px;text-align:center;color:var(--white)}
  .feature-icon{width:184px;height:184px;border-radius:50%;background:var(--white);margin:0 auto;display:flex;align-items:center;justify-content:center}
  .feature-icon span{width:166px;height:166px;border-radius:50%;background:var(--blue);display:flex;align-items:center;justify-content:center}
  .feature h3{font:700 30px/1 "Arimo",sans-serif;margin-top:56px}
  .feature p{font-size:19px;line-height:28px;margin-top:17px}

  /* products */
  .products-title{top:2022px;width:1200px;text-align:center;color:var(--blue)}
  .products-text{top:2090px;left:150px;width:900px;text-align:center;font-size:17px;line-height:47px}
  .card{position:absolute;top:2193px;width:238px;height:273px;border:2px solid var(--line);background:var(--white);text-align:center}
  .card.hover{background:#f1f1f1;box-shadow:0 2px 6px rgba(0,0,0,.12)}
  .card-img{width:190px;height:165px;margin:12px auto 0}
  .card h4{font:400 18px/1 "Arimo",sans-serif;color:var(--ink);margin-top:20px}
  .stars{color:var(--star);font-size:15px;letter-spacing:2px;margin-top:14px}
  .dots{display:flex;gap:14px}
  .dots span{width:11px;height:11px;border-radius:50%;background:var(--blue)}
  .dots span.on{background:var(--red)}

  /* testimonials */
  .testimonials{position:absolute;top:2616px;left:0;width:1200px;height:535px;
    background:linear-gradient(100deg,#39617a 0%,#3e6780 45%,#48708a 70%,#35607a 100%)}
  .testi-title{top:56px;width:1210px;text-align:center;color:var(--white);font-size:34px}
  .avatar{left:540px;top:145px;width:96px;height:96px;border-radius:50%;border:3px solid var(--white);background:radial-gradient(circle,#b89a84 0%,#8f7d73 100%)}
  .quote{font:700 110px/1 "Open Sans",serif;font-style:italic;color:var(--white)}
  .testi-text{top:282px;left:180px;width:820px;text-align:center;font:400 18px/31px "Open Sans",sans-serif;color:#e8eef2}
  .testi-name{top:405px;width:1176px;text-align:center;font:italic 400 22px/1 "Open Sans",sans-serif;color:#eef2f5}
  .testi-role{top:440px;width:1176px;text-align:center;font:italic 400 19px/1 "Open Sans",sans-serif;color:#eef2f5}
  .testi-dots{top:495px;left:564px;display:flex;gap:4px}
  .testi-dots span{width:12px;height:12px;border-radius:50%;background:var(--white)}

  /* news */
  .news-title{top:3246px;width:1196px;text-align:center}
  .news-card{position:absolute;top:3364px;width:475px;height:283px;background:var(--white);box-shadow:0 2px 12px rgba(0,0,0,.12)}
  .news-img{position:absolute;left:0;top:0;width:171px;height:283px}
  .news-body{position:absolute;left:205px;top:30px;width:245px}
  .news-body h5{font:400 20px/1 "Open Sans",sans-serif;color:var(--ink)}
  .news-date{font-size:13px;color:#555;margin-top:12px}
  .news-rule{width:60px;height:2px;background:#d9a1a6;margin-top:20px}
  .news-body p{font-size:13px;line-height:24px;color:#555;margin-top:18px}
  .news-foot{position:absolute;left:205px;right:20px;bottom:35px;display:flex;justify-content:space-between;align-items:center}
  .user-btn{width:28px;height:28px;border-radius:4px;background:var(--red);display:flex;align-items:center;justify-content:center}
  .side-dots{left:1115px;top:3466px;display:flex;flex-direction:column;gap:6px}
  .side-dots span{width:9px;height:9px;border-radius:50%;background:var(--red)}

  /* footer */
  .site-footer{position:absolute;top:3730px;left:0;width:1200px;height:436px;
    background:linear-gradient(160deg,#bb3540 0%,#b52a36 45%,#a8323a 100%)}
  .footer-curve{position:absolute;top:0;left:0}
  .footer-brand{top:140px;width:1200px;text-align:center;font:700 54px/1 "Arimo",sans-serif;color:var(--white);letter-spacing:2px}
  .footer-nav{top:232px;left:309px;display:flex;gap:37px;list-style:none;font-size:17px;color:var(--white)}
  .social{top:295px;left:533px;display:flex;gap:11px}
  .social span{width:38px;height:38px;border-radius:50%;border:2px solid var(--white)}
  .footer-rule{top:385px;height:1px;background:rgba(255,255,255,.7)}
  .copyright{top:376px;width:1200px;text-align:center;font-size:16px;color:var(--white)}
</style>
</head>
<body>
<div class="page">

  <header class="site-header">
    <div class="brand">U.S. TORVANE</div>
    <ul class="nav">
      <li class="active">HOME</li><li>ABOUT US</li><li>SERVICES</li><li>PRODUCTS</li><li>CONTACT US</li>
    </ul>
  </header>

  <section class="hero" role="img" aria-label="Soldiers in desert camouflage with a drone overhead on a sandy ridge">
    <h1 class="hero-title">U.S. TORVANE</h1>
    <p class="hero-sub">Neque porro quisquam est qui dolorem ipsum quia dolor sit amet,<br>consectetur, adipisci velitaa</p>
    <div class="btn-start">GET STARTED</div>
    <div class="hero-dots"><span></span><span></span><span></span></div>
  </section>
  <svg class="hero-curve" width="1200" height="160" viewBox="0 0 1200 160" aria-hidden="true">
    <path d="M0,55 Q600,181 1200,55 L1200,58 Q600,222 0,58 Z" fill="var(--blue)"/>
    <path d="M0,58 Q600,222 1200,58 L1200,160 L0,160 Z" fill="var(--white)"/>
  </svg>

  <h2 class="heading abs about-title">About <em>Us</em></h2>
  <p class="abs about-text">Lorem ipsum dolor sit amet, consectetur adipiscing elit, sed do eiusmod tempor incididunt ut labore et dolore magna aliqua. Ut enim ad minim veniam, quis nostrud exercitation ullamco laboris nisi ut aliquip ex ea commodo consequat. Duis aute irure dolor in reprehenderit in voluptate velit esse cillum dolore eu fugiat nulla pariatur. Excepteur sint occaecat cupidatat non proident, sunt in culpa qui officia deserunt mollit anim id est laborumSed ut perspiciatis unde omnis iste natus error sit voluptatem accusantium doloremque laudantium, totam rem aperiam, eaque ipsa quae ab illo inventore veritatis.</p>
  <div class="abs btn-more">READ MORE</div>
  <div class="abs about-arc"></div>
  <div class="abs about-photo" role="img" aria-label="Soldiers carrying a stretcher toward a helicopter on sandy ground"></div>

  <section class="why" role="img" aria-label="Dark background with a waving flag and an eagle">
    <h2 class="heading abs why-title">Why <em>Choose Us</em></h2>
    <div class="feature" style="left:125px">
      <div class="feature-icon"><span>
        <svg width="100" height="100" viewBox="0 0 100 100" fill="none" stroke="#fff" stroke-width="3">
          <path d="M22,10 H68 L80,22 V90 H22 Z"/><path d="M30,26 H58 M30,36 H70"/>
          <rect x="14" y="48" width="72" height="28" rx="3"/>
          <path d="M30,55 l3,6 6,1 -5,4 1,6 -5,-3 -5,3 1,-6 -5,-4 6,-1 Z M50,55 l3,6 6,1 -5,4 1,6 -5,-3 -5,3 1,-6 -5,-4 6,-1 Z M70,55 l3,6 6,1 -5,4 1,6 -5,-3 -5,3 1,-6 -5,-4 6,-1 Z"/>
        </svg></span></div>
      <h3>QUALITY</h3>
      <p>Lorem ipsum dolor sit amet,<br>consectetur adipiscing elit,</p>
    </div>
    <div class="feature" style="left:438px">
      <div class="feature-icon"><span>
        <svg width="100" height="100" viewBox="0 0 100 100" fill="none" stroke="#fff" stroke-width="3">
          <path d="M50,8 L84,20 V48 C84,70 68,84 50,92 C32,84 16,70 16,48 V20 Z"/>
          <path d="M50,30 L54,44 68,46 56,52 60,66 50,57 40,66 44,52 32,46 46,44 Z" fill="#fff"/>
        </svg></span></div>
      <h3>DURABILITY</h3>
      <p>Lorem ipsum dolor sit amet,<br>consectetur adipiscing elit,</p>
    </div>
    <div class="feature" style="left:768px">
      <div class="feature-icon"><span>
        <svg width="100" height="100" viewBox="0 0 100 100" fill="none" stroke="#fff" stroke-width="3">
          <path d="M50,10 L80,22 V48 C80,68 66,82 50,90 C34,82 20,68 20,48 V22 Z"/>
          <path d="M50,20 L71,29 V48 C71,63 61,73 50,79 C39,73 29,63 29,48 V29 Z"/>
          <circle cx="50" cy="50" r="11"/><path d="M44,50 l4,4 8,-8"/>
        </svg></span></div>
      <h3>RELIABILITY</h3>
      <p>Lorem ipsum dolor sit amet,<br>consectetur adipiscing elit,</p>
    </div>
  </section>

  <h2 class="heading abs products-title">Our <em>Products</em></h2>
  <p class="abs products-text">Lorem ipsum dolor sit amet, consectetur adipiscing elit, sed do eiusmod tempor incididunt ut labore et dolore magna aliqua. Ut enim ad minim veniam, quis nostrud exercitat</p>
  <div class="card" style="left:83px">
    <div class="card-img" role="img" aria-label="Grey camouflage tactical backpack" style="background:radial-gradient(ellipse at center,#9aa096 0%,#c9cbc4 55%,#fff 72%)"></div>
    <h4>PRODUCT NAME</h4><div class="stars">★★★★★</div>
  </div>
  <div class="card" style="left:349px">
    <div class="card-img" role="img" aria-label="Camouflage tactical pouch" style="background:radial-gradient(ellipse at center,#b4a27a 0%,#dcd3bd 50%,#fff 70%)"></div>
    <h4>PRODUCT NAME</h4><div class="stars">★★★★★</div>
  </div>
  <div class="card hover" style="left:614px">
    <div class="card-img" role="img" aria-label="Olive green canteens with pouches" style="background:linear-gradient(180deg,#4f5d3a 0%,#5e6b45 60%,#3f4a30 100%)"></div>
    <h4>PRODUCT NAME</h4><div class="stars">★★★★★</div>
  </div>
  <div class="card" style="left:880px">
    <div class="card-img" role="img" aria-label="Olive army hooded sweatshirt" style="background:radial-gradient(ellipse at center,#5f5f35 0%,#777748 45%,#fff 72%)"></div>
    <h4>PRODUCT NAME</h4><div class="stars">★★★★★</div>
  </div>
  <div class="abs dots" style="top:2535px;left:569px"><span></span><span></span><span class="on"></span></div>

  <section class="testimonials" role="img" aria-label="Blue-toned photo of soldiers beside a helicopter">
    <h2 class="heading abs testi-title">Testimonials</h2>
    <div class="abs avatar" role="img" aria-label="Customer portrait"></div>
    <div class="abs quote" style="left:150px;top:200px">“</div>
    <div class="abs quote" style="left:990px;top:345px">”</div>
    <p class="abs testi-text">Lorem ipsum dolor sit amet, consectetur adipiscing elit, sed do eiusmod tempor incididunt ut labore et dolore magna aliqua. Quis ipsum suspendisse ultrices gravida. Risus commodo viverra maecenas accumsan lacus vel facilisis.</p>
    <p class="abs testi-name">-DANIEL</p>
    <p class="abs testi-role">Neque porro quisquam</p>
    <div class="abs testi-dots"><span></span><span></span><span></span></div>
  </section>

  <h2 class="heading abs news-title">Latest <em>News</em></h2>
  <article class="news-card" style="left:113px">
    <div class="news-img" role="img" aria-label="Soldiers with a drone in the desert" style="background:linear-gradient(180deg,#b9bcbc 0%,#a99a80 55%,#7d6b52 100%)"></div>
    <div class="news-body">
      <h5>Lorem ipsum is best</h5>
      <div class="news-date">on April 28, 2020 9:58 AM</div>
      <div class="news-rule"></div>
      <p>Lorem ipsum dolor sit amet, consectetur adipiscing elit, sed do eiusmod tempor incididunt ut labore</p>
    </div>
    <div class="news-foot">
      <svg width="14" height="12" viewBox="0 0 14 12" fill="none" stroke="#999" stroke-width="1.3"><rect x="1" y="1" width="12" height="8"/><path d="M4,11 H10"/></svg>
      <div class="user-btn"><svg width="18" height="18" viewBox="0 0 18 18" fill="none" stroke="#fff" stroke-width="1.8"><circle cx="9" cy="6" r="3.5"/><path d="M2,17 C2,12 5,10.5 9,10.5 C13,10.5 16,12 16,17"/><rect x="1" y="1" width="16" height="16" rx="2"/></svg></div>
    </div>
  </article>
  <article class="news-card" style="left:619px">
    <div class="news-img" role="img" aria-label="Soldier kneeling by a helicopter" style="background:linear-gradient(180deg,#5d5a4a 0%,#6f6450 50%,#8b6d46 100%)"></div>
    <div class="news-body">
      <h5>Lorem ipsum is best</h5>
      <div class="news-date">on April 28, 2020 9:58 AM</div>
      <div class="news-rule"></div>
      <p>Lorem ipsum dolor sit amet, consectetur adipiscing elit, sed do eiusmod tempor incididunt ut labore</p>
    </div>
    <div class="news-foot">
      <svg width="14" height="12" viewBox="0 0 14 12" fill="none" stroke="#999" stroke-width="1.3"><rect x="1" y="1" width="12" height="8"/><path d="M4,11 H10"/></svg>
      <div class="user-btn"><svg width="18" height="18" viewBox="0 0 18 18" fill="none" stroke="#fff" stroke-width="1.8"><circle cx="9" cy="6" r="3.5"/><path d="M2,17 C2,12 5,10.5 9,10.5 C13,10.5 16,12 16,17"/><rect x="1" y="1" width="16" height="16" rx="2"/></svg></div>
    </div>
  </article>
  <div class="abs side-dots"><span></span><span></span><span></span></div>

  <footer class="site-footer" role="img" aria-label="Red-toned photo of soldiers and a helicopter">
    <svg class="footer-curve" width="1200" height="110" viewBox="0 0 1200 110" aria-hidden="true">
      <path d="M0,0 H1200 V102 Q600,-72 0,102 Z" fill="var(--white)"/>
      <path d="M0,102 Q600,-72 1200,102 L1200,96 Q600,-92 0,96 Z" fill="var(--blue)"/>
    </svg>
    <div class="abs footer-brand">U.S. TORVANE</div>
    <ul class="abs footer-nav"><li>HOME</li><li>ABOUT US</li><li>SERVICES</li><li>PRODUCTS</li><li>CONTACT US</li></ul>
    <div class="abs social"><span></span><span></span><span></span></div>
    <div class="abs footer-rule" style="left:113px;width:335px"></div>
    <div class="abs footer-rule" style="left:755px;width:335px"></div>
    <p class="abs copyright">Copyrights 2020. All rights reserved</p>
  </footer>

</div>
</body>
</html>
```